Diabetes control iOS/Android app design

I need a modern app design with light colors that are easy on the eyes, This app is for diabetes control. Focusing on Sweet/carb control and its daily intake .. I have uploaded some wireframe pages to design . Light colors are preferred for design. I donot need too much Hussle and data on main page.
Name/title: Glimwell- Diabetes reversal

Target Market(s)

Diabetes patients

Industry/Entity Type

health

Colors
0094D4
00A9DD
6FCCEA
C7EBF8
E9F6FB
00AB8E
00BBA5
67D7C9
C6EFE9
E9F9F6
59FF00
82FF00
B8FF75
E3FFCB
F4FFEA
FFC000
F8CF3A
FAE287
FDF2CF
FEFAEE

Requirements
Should not have
• complicated design. It should be simple , modern and easy o eye.

```html
<!DOCTYPE html>
<html lang="en">
<head>
<meta charset="utf-8">
<title>Glimwell – Diabetes Control App Design</title>
<link rel="stylesheet" href="https://fonts.googleapis.com/css2?family=Inter:wght@400;500;600;700;800&display=swap">
<style>
:root{
  --blue:#0094D4;
  --blue-2:#00A9DD;
  --blue-3:#6FCCEA;
  --blue-4:#C7EBF8;
  --blue-5:#E9F6FB;
  --teal:#00AB8E;
  --yellow:#FFC000;
  --orange:#F89A3A;
  --red:#F05A3A;
  --ink:#1E2A38;
  --muted:#8A96A3;
  --line:#E3E8EE;
  --page:#EEF1F4;
  --card:#FFFFFF;
}
*{box-sizing:border-box;margin:0;padding:0}
html,body{width:1200px;height:2400px;overflow:hidden}
body{background:var(--page);font-family:"Inter",sans-serif;color:var(--ink);position:relative}

.board-title{position:absolute;top:62px;left:0;width:100%;text-align:center;font-size:32px;font-weight:800;letter-spacing:.5px;color:var(--ink)}
.meta{position:absolute;top:142px;font-size:9px;letter-spacing:1px;color:var(--muted);text-align:center}
.meta strong{display:block;font-size:15px;color:var(--ink);letter-spacing:1px;margin-top:4px;font-weight:700}
.meta--fonts{left:560px;width:80px}
.meta--tools{left:680px;width:60px}
.tool-mark{display:block;width:14px;height:14px;border-radius:50%;background:var(--ink);margin:6px auto 0}

.hero-scene{position:absolute;top:190px;left:0;width:1200px;height:600px;
  background:linear-gradient(180deg,#E6E8EA 0%,#D9DBDD 55%,#B88B5E 56%,#A5774B 72%,#8E6440 100%)}

.section-label{position:absolute;font-size:8px;font-weight:600;letter-spacing:.8px;color:var(--muted);text-transform:uppercase}

/* screen */
.screen{position:absolute;background:var(--card);border-radius:22px;border:1px solid #D6DCE3;
  box-shadow:0 10px 28px rgba(30,42,56,.14);overflow:hidden;display:flex;flex-direction:column;font-size:7px}
.status{height:16px;display:flex;justify-content:space-between;align-items:center;padding:0 14px;font-size:6px;font-weight:600}
.status .bars{width:22px;height:5px;border-radius:2px;background:var(--ink)}
.topbar{display:flex;align-items:center;padding:4px 10px;gap:6px}
.topbar .back{width:14px;height:14px;border-radius:50%;background:var(--blue-5);color:var(--blue);font-size:10px;line-height:13px;text-align:center}
.topbar h3{flex:1;text-align:center;font-size:9px;font-weight:600;margin-right:20px}
.body{flex:1;padding:6px 10px;display:flex;flex-direction:column;gap:7px}
.card{background:var(--card);border:1px solid var(--line);border-radius:10px;padding:7px}
.card-title{font-size:7px;font-weight:600;margin-bottom:4px}
.muted{color:var(--muted);font-size:6px;line-height:1.45}
.chart{display:block;width:100%}
.legend{display:flex;gap:8px;font-size:5.5px;color:var(--muted);margin-top:3px}
.legend i{display:inline-block;width:5px;height:5px;border-radius:50%;margin-right:2px;vertical-align:middle}
.navbar{height:30px;border-top:1px solid var(--line);display:flex;justify-content:space-around;align-items:center;padding:0 10px}
.navbar span{width:9px;height:9px;border-radius:3px;background:#C5CED8}
.navbar span.active{background:var(--blue)}
.navbar span.fab{width:20px;height:20px;border-radius:50%;background:var(--blue);margin-top:-10px;box-shadow:0 3px 8px rgba(0,148,212,.4)}

.gauge{display:block;width:88%;margin:0 auto}
.food-row{display:flex;align-items:center;gap:6px;padding:4px 0;border-bottom:1px solid var(--line);font-size:6.5px}
.food-row b{font-weight:600;flex:1}
.food-row em{font-style:normal;color:var(--muted)}
.food-icon{width:14px;height:14px;border-radius:4px;background:var(--blue-4)}
.food-icon.y{background:#FDF2CF}.food-icon.g{background:#C6EFE9}

.info-box{display:flex;gap:6px;background:var(--blue-5);border-radius:10px;padding:7px;align-items:flex-start}
.info-dot{flex:none;width:14px;height:14px;border-radius:50%;background:var(--blue);color:#fff;font-size:8px;text-align:center;line-height:14px;font-weight:700}
.field-label{font-size:6.5px;font-weight:600;margin-top:4px}
.field{border:1px solid var(--line);border-radius:7px;padding:6px;font-size:6.5px;display:flex;justify-content:space-between;color:var(--ink)}
.actions{display:flex;gap:6px;margin-top:auto;padding-bottom:10px}
.btn{flex:1;text-align:center;border-radius:8px;padding:6px 0;font-size:7px;font-weight:600}
.btn--ghost{border:1px solid var(--blue);color:var(--blue)}
.btn--solid{background:var(--blue);color:#fff}

.option{display:flex;align-items:center;gap:6px;border:1px solid var(--line);border-radius:8px;padding:5px 6px;font-size:6.5px}
.option .thumb{width:16px;height:16px;border-radius:5px;background:#FDF2CF}
.option b{flex:1;font-weight:600}
.option .check{width:9px;height:9px;border-radius:50%;border:1px solid #C5CED8}
.option.selected{border-color:var(--blue)}
.option.selected .check{background:var(--blue);border-color:var(--blue)}

.ring{position:relative;width:84px;height:84px;margin:4px auto 0}
.ring svg{width:100%;height:100%}
.ring .value{position:absolute;inset:0;display:flex;flex-direction:column;align-items:center;justify-content:center;font-size:18px;font-weight:700;color:var(--blue)}
.ring .value small{font-size:5.5px;color:var(--muted);font-weight:500}
.center{text-align:center}
.qa-card{background:var(--blue-5);border-radius:10px;padding:7px}
.qa-card .card-title{display:flex;align-items:center;gap:4px}

.streak{display:flex;flex-direction:column;align-items:center;gap:3px;margin-top:8px}
.streak svg{width:34px;height:42px}
.streak .num{font-size:24px;font-weight:700}
.streak .lbl{font-size:7px;color:var(--muted)}
.pill{display:flex;align-items:center;justify-content:center;gap:5px;border-radius:10px;background:var(--blue-5);color:var(--blue);padding:7px;font-size:7px;font-weight:600;margin-top:8px}
.pill i{width:8px;height:8px;border-radius:50%;background:var(--blue)}
.days{display:flex;justify-content:space-between;margin-top:6px}
.days span{width:14px;height:14px;border-radius:50%;background:var(--blue-5);font-size:5.5px;text-align:center;line-height:14px;color:var(--blue)}
.days span.on{background:var(--blue);color:#fff}

.splash{justify-content:center;align-items:center;gap:8px;background:linear-gradient(180deg,#FFFFFF 0%,var(--blue-5) 100%)}
.brand{display:flex;align-items:center;gap:8px}
.brand-square{width:26px;height:26px;border-radius:6px;background:var(--blue)}
.brand-square.orange{background:var(--orange)}
.brand-square.red{background:var(--red)}
.brand-name{font-size:20px;font-weight:800;color:var(--blue);letter-spacing:.5px}
.tagline{font-size:6px;color:var(--muted)}
.splash .status{position:absolute;top:0;left:0;right:0}

.footer{position:absolute;top:2345px;width:100%;text-align:center;font-size:18px;font-weight:800;letter-spacing:1px;color:#DDE2E7}

/* placement */
.hero-1{left:262px;top:300px;width:180px;height:360px;z-index:1}
.hero-2{left:372px;top:278px;width:190px;height:390px;z-index:2}
.hero-3{left:495px;top:250px;width:215px;height:450px;z-index:4}
.hero-4{left:672px;top:278px;width:190px;height:390px;z-index:3}
.hero-5{left:800px;top:300px;width:180px;height:360px;z-index:2}
.s-sugar{left:190px;top:850px;width:180px;height:360px}
.s-monitor{left:390px;top:850px;width:200px;height:400px}
.s-plan{left:620px;top:850px;width:180px;height:360px}
.s-splash-1{left:920px;top:850px;width:180px;height:360px}
.s-splash-2{left:920px;top:1240px;width:180px;height:360px}
.s-time{left:190px;top:1670px;width:180px;height:360px}
.s-profile{left:390px;top:1670px;width:200px;height:440px}
.s-goals{left:620px;top:1670px;width:180px;height:360px}
.s-splash-3{left:920px;top:1840px;width:180px;height:360px}
</style>
</head>
<body>

<h1 class="board-title">DIABETES CONTROL IOS/ANDROID APP DESIGN</h1>
<div class="meta meta--fonts">FONTS<strong>INTER</strong></div>
<div class="meta meta--tools">TOOLS<span class="tool-mark"></span></div>

<div class="hero-scene" role="img" aria-label="Soft grey wall above a wooden tabletop where the app screens are displayed"></div>

<!-- hero screens -->
<section class="screen hero-1">
  <div class="status"><span>9:41</span><span class="bars"></span></div>
  <div class="topbar"><span class="back">‹</span><h3>Goals</h3></div>
  <div class="body">
    <p class="muted center">Days without sugar</p>
    <div class="streak">
      <svg viewBox="0 0 34 42"><path d="M17 2C20 12 30 16 30 28A13 13 0 0 1 4 28C4 20 10 16 11 8C14 12 15 14 17 2Z" fill="#F89A3A"/><path d="M17 20C19 25 23 27 23 32A6 6 0 0 1 11 32C11 28 15 25 17 20Z" fill="#FFC000"/></svg>
      <span class="num">8</span><span class="lbl">Days Streak</span>
    </div>
    <div class="days"><span class="on">M</span><span class="on">T</span><span class="on">W</span><span>T</span><span>F</span><span>S</span><span>S</span></div>
  </div>
  <nav class="navbar"><span class="active"></span><span></span><span class="fab"></span><span></span><span></span></nav>
</section>

<section class="screen hero-2">
  <div class="status"><span>9:41</span><span class="bars"></span></div>
  <div class="topbar"><span class="back">‹</span><h3>Profile</h3></div>
  <div class="body">
    <div class="ring">
      <svg viewBox="0 0 84 84"><circle cx="42" cy="42" r="36" fill="none" stroke="#C7EBF8" stroke-width="7"/><circle cx="42" cy="42" r="36" fill="none" stroke="#0094D4" stroke-width="7" stroke-linecap="round" stroke-dasharray="170 226" transform="rotate(-90 42 42)"/></svg>
      <div class="value">200<small>calories left</small></div>
    </div>
    <p class="muted center">Keep your daily sugar low and steady.</p>
    <div class="qa-card"><div class="card-title"><span class="info-dot">?</span>What is Sugar?</div><p class="muted">Sugar is a simple carb that raises blood glucose fast.</p></div>
  </div>
  <nav class="navbar"><span></span><span></span><span class="fab"></span><span></span><span class="active"></span></nav>
</section>

<section class="screen hero-3">
  <div class="status"><span>9:41</span><span class="bars"></span></div>
  <div class="topbar"><span class="back">‹</span><h3>Sugar Count</h3></div>
  <div class="body">
    <svg class="gauge" viewBox="0 0 160 96">
      <path d="M20 80A60 60 0 0 1 50 28" fill="none" stroke="#FFC000" stroke-width="22"/>
      <path d="M50 28A60 60 0 0 1 110 28" fill="none" stroke="#F89A3A" stroke-width="22"/>
      <path d="M110 28A60 60 0 0 1 140 80" fill="none" stroke="#F05A3A" stroke-width="22"/>
      <circle cx="80" cy="76" r="22" fill="#0094D4"/>
      <text x="80" y="84" text-anchor="middle" font-family="Inter, sans-serif" font-size="22" font-weight="700" fill="#fff">4</text>
    </svg>
    <div class="card">
      <div class="card-title">Daily Sugar Rate Graph</div>
      <svg class="chart" viewBox="0 0 160 70"><path d="M0 50C15 20 25 60 40 40S65 15 80 35 105 55 120 30 145 20 160 40V70H0Z" fill="#E9F6FB"/><path d="M0 50C15 20 25 60 40 40S65 15 80 35 105 55 120 30 145 20 160 40" fill="none" stroke="#0094D4" stroke-width="2"/></svg>
    </div>
  </div>
  <nav class="navbar"><span class="active"></span><span></span><span class="fab"></span><span></span><span></span></nav>
</section>

<section class="screen hero-4">
  <div class="status"><span>9:41</span><span class="bars"></span></div>
  <div class="topbar"><span class="back">‹</span><h3>Rehab Monitors</h3></div>
  <div class="body">
    <div class="card">
      <div class="card-title">Daily Sugar Graph</div>
      <svg class="chart" viewBox="0 0 160 56"><path d="M0 40C20 10 35 45 55 28S85 12 100 30 130 44 160 18" fill="none" stroke="#0094D4" stroke-width="2"/><path d="M0 46C20 30 40 50 60 38S95 30 115 40 140 34 160 32" fill="none" stroke="#6FCCEA" stroke-width="1.5"/></svg>
    </div>
    <div class="card">
      <div class="card-title">Daily Meal Activities</div>
      <svg class="chart" viewBox="0 0 160 60"><g fill="#0094D4"><rect x="6" y="30" width="12" height="30" rx="2"/><rect x="28" y="14" width="12" height="46" rx="2"/><rect x="50" y="36" width="12" height="24" rx="2"/><rect x="72" y="8" width="12" height="52" rx="2"/><rect x="94" y="24" width="12" height="36" rx="2"/><rect x="116" y="40" width="12" height="20" rx="2"/><rect x="138" y="18" width="12" height="42" rx="2"/></g></svg>
    </div>
  </div>
  <nav class="navbar"><span></span><span class="active"></span><span class="fab"></span><span></span><span></span></nav>
</section>

<section class="screen hero-5">
  <div class="status"><span>9:41</span><span class="bars"></span></div>
  <div class="topbar"><span class="back">‹</span><h3>Rehab Plan</h3></div>
  <div class="body">
    <div class="info-box"><span class="info-dot">i</span><p class="muted">We are able to arrange you a custom plan.</p></div>
    <p class="field-label">Choose starting date</p>
    <div class="field"><span>12 Mar 2024</span><span>▾</span></div>
    <div class="actions"><span class="btn btn--ghost">Back</span><span class="btn btn--solid">Next</span></div>
  </div>
</section>

<!-- screen grid -->
<span class="section-label" style="left:190px;top:834px">Sugar Count</span>
<section class="screen s-sugar">
  <div class="status"><span>9:41</span><span class="bars"></span></div>
  <div class="topbar"><span class="back">‹</span><h3>Sugar Count</h3></div>
  <div class="body">
    <svg class="gauge" viewBox="0 0 160 96">
      <path d="M20 80A60 60 0 0 1 50 28" fill="none" stroke="#FFC000" stroke-width="22"/>
      <path d="M50 28A60 60 0 0 1 110 28" fill="none" stroke="#F89A3A" stroke-width="22"/>
      <path d="M110 28A60 60 0 0 1 140 80" fill="none" stroke="#F05A3A" stroke-width="22"/>
      <circle cx="80" cy="76" r="22" fill="#0094D4"/>
      <text x="80" y="84" text-anchor="middle" font-family="Inter, sans-serif" font-size="22" font-weight="700" fill="#fff">4</text>
    </svg>
    <div class="card">
      <div class="card-title">Daily Sugar Rate Graph</div>
      <svg class="chart" viewBox="0 0 160 80"><path d="M0 55C15 25 25 65 40 45S65 20 80 40 105 60 120 35 145 25 160 45V80H0Z" fill="#E9F6FB"/><path d="M0 55C15 25 25 65 40 45S65 20 80 40 105 60 120 35 145 25 160 45" fill="none" stroke="#0094D4" stroke-width="2"/></svg>
      <div class="legend"><span><i style="background:var(--blue)"></i>Sugar</span><span><i style="background:var(--blue-3)"></i>Target</span></div>
    </div>
  </div>
  <nav class="navbar"><span class="active"></span><span></span><span class="fab"></span><span></span><span></span></nav>
</section>

<span class="section-label" style="left:390px;top:834px">Rehab Monitors</span>
<section class="screen s-monitor">
  <div class="status"><span>9:41</span><span class="bars"></span></div>
  <div class="topbar"><span class="back">‹</span><h3>Rehab Monitors</h3></div>
  <div class="body">
    <div class="card">
      <div class="card-title">Daily Sugar Graph</div>
      <svg class="chart" viewBox="0 0 160 56"><path d="M0 40C20 10 35 45 55 28S85 12 100 30 130 44 160 18" fill="none" stroke="#0094D4" stroke-width="2"/><path d="M0 46C20 30 40 50 60 38S95 30 115 40 140 34 160 32" fill="none" stroke="#6FCCEA" stroke-width="1.5"/></svg>
      <div class="legend"><span><i style="background:var(--blue)"></i>This week</span><span><i style="background:var(--blue-3)"></i>Last week</span></div>
    </div>
    <div class="card">
      <div class="card-title">Daily Meal Activities</div>
      <svg class="chart" viewBox="0 0 160 60"><g fill="#0094D4"><rect x="6" y="30" width="12" height="30" rx="2"/><rect x="28" y="14" width="12" height="46" rx="2"/><rect x="50" y="36" width="12" height="24" rx="2"/><rect x="72" y="8" width="12" height="52" rx="2"/><rect x="94" y="24" width="12" height="36" rx="2"/><rect x="116" y="40" width="12" height="20" rx="2"/><rect x="138" y="18" width="12" height="42" rx="2"/></g></svg>
    </div>
    <div>
      <div class="card-title">Daily Food</div>
      <div class="food-row"><span class="food-icon y"></span><b>Breakfast</b><em>45 g</em></div>
      <div class="food-row"><span class="food-icon g"></span><b>Lunch</b><em>60 g</em></div>
      <div class="food-row"><span class="food-icon"></span><b>Dinner</b><em>38 g</em></div>
    </div>
  </div>
  <nav class="navbar"><span></span><span class="active"></span><span class="fab"></span><span></span><span></span></nav>
</section>

<span class="section-label" style="left:620px;top:834px">Rehab Plan</span>
<section class="screen s-plan">
  <div class="status"><span>9:41</span><span class="bars"></span></div>
  <div class="topbar"><span class="back">‹</span><h3>Rehab Plan</h3></div>
  <div class="body">
    <div class="info-box"><span class="info-dot">i</span><p class="muted">We are able to arrange you a custom plan for diabetes control.</p></div>
    <p class="field-label">Choose starting date</p>
    <div class="field"><span>12 Mar 2024</span><span>▾</span></div>
    <div class="actions"><span class="btn btn--ghost">Back</span><span class="btn btn--solid">Next</span></div>
  </div>
</section>

<span class="section-label" style="left:920px;top:834px">Load Device</span>
<section class="screen splash s-splash-1">
  <div class="status"><span>9:41</span><span class="bars"></span></div>
  <div class="brand"><span class="brand-square"></span><span class="brand-name">GLIMWELL</span></div>
  <p class="tagline">Glimwell- Diabetes reversal</p>
</section>

<section class="screen splash s-splash-2">
  <div class="status"><span>9:41</span><span class="bars"></span></div>
  <div class="brand"><span class="brand-square orange"></span><span class="brand-name">GLIMWELL</span></div>
  <p class="tagline">Glimwell- Diabetes reversal</p>
</section>

<span class="section-label" style="left:190px;top:1654px">Rehab Plan - Time</span>
<section class="screen s-time">
  <div class="status"><span>9:41</span><span class="bars"></span></div>
  <div class="topbar"><span class="back">‹</span><h3>Rehab Plan</h3></div>
  <div class="body">
    <p class="field-label center">Choose a suggested time</p>
    <div class="option selected"><span class="thumb"></span><b>Morning Plan</b><span class="check"></span></div>
    <div class="option"><span class="thumb"></span><b>Noon Plan</b><span class="check"></span></div>
    <div class="option"><span class="thumb"></span><b>Evening Plan</b><span class="check"></span></div>
    <div class="actions"><span class="btn btn--ghost">Back</span><span class="btn btn--solid">Next</span></div>
  </div>
</section>

<span class="section-label" style="left:390px;top:1654px">Profile</span>
<section class="screen s-profile">
  <div class="status"><span>9:41</span><span class="bars"></span></div>
  <div class="topbar"><span class="back">‹</span><h3>Profile</h3></div>
  <div class="body">
    <div class="ring">
      <svg viewBox="0 0 84 84"><circle cx="42" cy="42" r="36" fill="none" stroke="#C7EBF8" stroke-width="7"/><circle cx="42" cy="42" r="36" fill="none" stroke="#0094D4" stroke-width="7" stroke-linecap="round" stroke-dasharray="170 226" transform="rotate(-90 42 42)"/></svg>
      <div class="value">200<small>calories left</small></div>
    </div>
    <p class="muted center">Keep your daily sugar intake low and steady to reach your weekly goal.</p>
    <div class="qa-card">
      <div class="card-title"><span class="info-dot">?</span>What is Sugar?</div>
      <p class="muted">Sugar is a simple carb that raises blood glucose fast. Small swaps in drinks and snacks help you stay inside your daily limit and feel better.</p>
    </div>
    <div class="card">
      <div class="card-title">Last Update</div>
      <svg class="chart" viewBox="0 0 160 50"><path d="M0 38C20 18 35 42 55 26S85 10 105 28 135 36 160 16" fill="none" stroke="#0094D4" stroke-width="2"/></svg>
    </div>
  </div>
  <nav class="navbar"><span></span><span></span><span class="fab"></span><span></span><span class="active"></span></nav>
</section>

<span class="section-label" style="left:620px;top:1654px">Goals</span>
<section class="screen s-goals">
  <div class="status"><span>9:41</span><span class="bars"></span></div>
  <div class="topbar"><span class="back">‹</span><h3>Goals</h3></div>
  <div class="body">
    <p class="muted center">Days without sugar</p>
    <div class="streak">
      <svg viewBox="0 0 34 42"><path d="M17 2C20 12 30 16 30 28A13 13 0 0 1 4 28C4 20 10 16 11 8C14 12 15 14 17 2Z" fill="#F89A3A"/><path d="M17 20C19 25 23 27 23 32A6 6 0 0 1 11 32C11 28 15 25 17 20Z" fill="#FFC000"/></svg>
      <span class="num">8</span><span class="lbl">Days Streak</span>
    </div>
    <div class="pill"><i></i>Stay sugar free today</div>
  </div>
  <nav class="navbar"><span class="active"></span><span></span><span class="fab"></span><span></span><span></span></nav>
</section>

<section class="screen splash s-splash-3">
  <div class="status"><span>9:41</span><span class="bars"></span></div>
  <div class="brand"><span class="brand-square red"></span><span class="brand-name">GLIMWELL</span></div>
  <p class="tagline">Glimwell- Diabetes reversal</p>
</section>

<p class="footer">THANK YOU FOR WATCHING MY WORKS</p>

</body>
</html>
```